Book Title: “Faith: Road of Endless Grace” Please see the attachment “Text on the cover”.

Book Cover Design Instructions: This book is meant for people of all religions and nationalities. Therefore, on the cover, there should be no mosque or an object specific to any religion. The primary emphasis should be on the "unconditional love of God." Therefore, use universal symbols of love. The second priority themes could be Sufism, Peace, and self-improvement. Rest is your imagination. Please also see the attachment: 'Book description and author's Bio.'
This book has the potential to be a best seller. Please do a good job.
What Book Cover Formats are required: A designer should submit cover designs in three formats: (1) eBook, (2) Paperback, and (3) Hardback. These books will be published on Borvex QPL.
Format requirements for eBooks are available from: https://qpl.borvex.example/en_US/help/topic/R731928457.
You can find paperback and hardback cover measurements from: https://qpl.borvex.example/en_US/cover-calculator
• To complete the project, all three formats should be accepted by Borvex QPL.
• The book interior trim size is 6.14 X 9.21 inches.
• Interior Type: Premium color.
• No bleed.
• I do not upload barcode. So, the back cover should have room for Borvex to print the barcode.
• Number of pages 126.
Compensation for the designer: After selecting one designer, I will increase the amount by $200 on Artvelle to compensate for three deliverables.
Follow-up of the Project:
After the book is published, I may need minor revisions. For example, the number of pages may change. Therefore, I will need the same design in revised sizes. In that case, I will pay $25 for each revision. For example, if the number of pages changes, I will need a different spine for paperback and hardback, then I will pay the artist $25 + $25 = $50 for both designs.
List of Enclosers:
1. Text on the cover.
2. Book description and author's Bio for the back cover.
3. Later, I will upload my picture for the book's back cover.

Target Market(s)

Any adult

Industry/Entity Type

Any industry

Requirements
Must have
• Three Deliverables

```html
<!DOCTYPE html>
<html lang="en">
<head>
<meta charset="utf-8">
<title>Faith: Road of Endless Grace — Book Cover</title>
<link rel="stylesheet" href="https://fonts.googleapis.com/css2?family=Montserrat:wght@500;600;700&display=swap">
<style>
  :root {
    --page-bg: #efefef;
    --cover-black: #0d0d0f;
    --cover-top: #18181b;
    --gold: #d49b5f;
    --white: #ffffff;
    --rule: #55555a;
    --scene-sky: #0a1513;
    --scene-dusk: #16221e;
    --scene-glow: #c9974f;
    --scene-arcade: #7a5a34;
    --scene-floor: #bdb8ae;
    --scene-floor-deep: #8f8a80;
  }
  * { margin: 0; padding: 0; box-sizing: border-box; }
  html, body {
    width: 1200px;
    height: 963px;
    overflow: hidden;
    background: var(--page-bg);
    font-family: "Montserrat", Arial, sans-serif;
  }
  .canvas {
    position: relative;
    width: 1200px;
    height: 963px;
  }
  .book-cover {
    position: absolute;
    left: 298px;
    top: 56px;
    width: 571px;
    height: 854px;
    background: linear-gradient(180deg, var(--cover-top) 0%, var(--cover-black) 55%);
    overflow: hidden;
    text-align: center;
  }
  .author-name {
    position: absolute;
    top: 47px;
    left: 0;
    width: 100%;
    color: var(--white);
    font-weight: 600;
    font-size: 19px;
    line-height: 1;
    letter-spacing: 0.62em;
    padding-left: 0.62em;
  }
  .title-main {
    position: absolute;
    top: 108px;
    left: 0;
    width: 100%;
    color: var(--gold);
    font-weight: 600;
    font-size: 160px;
    line-height: 1;
    letter-spacing: -0.01em;
    text-shadow: 0 5px 12px rgba(0,0,0,0.65);
  }
  .title-sub {
    position: absolute;
    top: 263px;
    left: 0;
    width: 100%;
    color: var(--white);
    font-weight: 500;
    font-size: 40px;
    line-height: 1;
    letter-spacing: -0.015em;
  }
  .tagline-block {
    position: absolute;
    top: 341px;
    left: 0;
    width: 100%;
  }
  .tagline-rule {
    width: 250px;
    height: 2px;
    margin: 0 auto;
    background: linear-gradient(90deg, transparent, var(--rule) 25%, var(--rule) 75%, transparent);
  }
  .tagline {
    color: var(--gold);
    font-weight: 500;
    font-size: 15px;
    line-height: 20px;
    padding: 7px 0 7px;
    white-space: nowrap;
  }
  .tagline strong { font-weight: 600; }
  .cover-scene {
    position: absolute;
    left: 0;
    top: 442px;
    width: 100%;
    height: 412px;
    background: linear-gradient(180deg,
      var(--scene-sky) 0%,
      var(--scene-dusk) 28%,
      #2c2a22 38%,
      var(--scene-arcade) 46%,
      var(--scene-glow) 53%,
      #6e5f4c 60%,
      #a19c92 70%,
      var(--scene-floor) 84%,
      var(--scene-floor-deep) 100%);
  }
</style>
</head>
<body>
  <main class="canvas">
    <section class="book-cover">
      <p class="author-name">DR. NOREEN VALSARI</p>
      <h1 class="title-main">FAITH</h1>
      <h2 class="title-sub">Road of Endless Grace</h2>
      <div class="tagline-block">
        <div class="tagline-rule"></div>
        <p class="tagline">Guide to<br><strong>Cultivating Inner Peace and Mindful Living</strong></p>
        <div class="tagline-rule"></div>
      </div>
      <div class="cover-scene" role="img" aria-label="Cover photograph: a vast illuminated courtyard at night with glowing arcades and tall lit towers, filled with a great gathering of people arranged in concentric circles — imagery of unity, peace and shared devotion"></div>
    </section>
  </main>
</body>
</html>
```